Web site for radio show

I've got a radio show starting on OrbitalWave and need a web site for it. I am familiar with WordPress, so I'd like to get a design for a WordPress-based web site for the show.

I'm also posting a logo project to be done at the same time.

The best radio show web site I've seen is the Cosmic Tuesday site (www.cosmictuesday-example.com). That's a good model but I don't want to start with that much complexity and content. The initial site that I'd like you to design would have the following parts:
- Upcoming shows
- Past shows (including links to authors, their web sites, and their books)
- Chirper feed
- Blog
- About
- ...and anything else you think would be necessary

For colors, I'd like it to be consistent with my personal web site: www.kellaway-ventures-example.com

Target Market(s)

The target market for this show is mid- to upper-level managers

Industry/Entity Type

Radio

Requirements
Must have
• The project has to proceed in (at least) two stages: a first rough layout, and a second finished design. Whether you want a third stage in between with look and feel options is up to you.

```html
<!DOCTYPE html>
<html lang="en">
<head>
<meta charset="utf-8">
<title>Halvorsen Show</title>
<link href="https://fonts.googleapis.com/css2?family=Raleway:wght@200;300;400;600&family=Open+Sans:wght@400;600&display=swap" rel="stylesheet">
<style>
:root{
  --red:#cf2230;
  --ink:#333;
  --muted:#777;
  --band:#ededed;
  --band-dark:#e2e2e2;
  --card:#f6f6f6;
  --footer:#4a4a4a;
  --hero-a:#151515;
  --hero-b:#3a2f2a;
}
*{box-sizing:border-box;margin:0;padding:0}
html,body{width:1200px;height:2240px;overflow:hidden;background:#fff}
body{font-family:'Open Sans',Arial,sans-serif;color:var(--ink);font-size:14px;position:relative}
.site-header{height:140px;position:relative}
.brand{position:absolute;left:56px;top:40px;font-family:'Raleway',sans-serif;font-weight:600;font-size:34px;line-height:40px;color:var(--ink);text-transform:uppercase}
.search{position:absolute;left:790px;top:26px;width:330px;height:30px;border:1px solid #ccc;font-size:13px;color:#999;padding:6px 10px}
.search svg{position:absolute;right:8px;top:7px}
.main-nav{position:absolute;right:80px;top:100px;display:flex;gap:22px;font-size:13px;text-transform:uppercase}
.main-nav a{color:var(--ink);text-decoration:none}
.main-nav a.active{color:var(--red)}
.hero{position:absolute;top:140px;left:0;width:1200px;height:420px;background:linear-gradient(90deg,var(--hero-a) 0%,#222 40%,var(--hero-b) 70%,#1c1c1c 100%)}
.hero-text{position:absolute;left:160px;top:118px;font-family:'Raleway',sans-serif;font-weight:300;font-size:46px;line-height:52px;text-transform:uppercase}
.hero-text .lead{color:var(--red)}
.hero-text .rest{color:#fff}
.btn{display:inline-block;background:var(--red);color:#fff;font-size:15px;padding:12px 24px}
.hero .btn{position:absolute;left:160px;top:310px}
.hero-arrow{position:absolute;top:190px;width:36px;height:56px;background:rgba(255,255,255,.15);border:1px solid rgba(255,255,255,.5)}
.hero-arrow.left{left:16px}.hero-arrow.right{right:16px}
.section-title{font-family:'Raleway',sans-serif;font-weight:300;color:var(--red);font-size:46px;text-align:center}
.about{position:absolute;top:560px;left:0;width:1200px;height:300px}
.about .section-title{margin-top:50px}
.about p{width:940px;margin:22px auto 0;text-align:center;font-size:17px;line-height:26px;color:var(--muted)}
.upcoming{position:absolute;top:860px;left:0;width:1200px;height:500px;background:var(--band)}
.upcoming .section-title{margin-top:40px}
.pager{position:absolute;right:80px;display:flex;gap:6px}
.pager i{width:22px;height:22px;background:#bbb;display:block}
.show-row{position:absolute;top:120px;left:120px;display:flex;gap:150px}
.show{width:220px}
.show .photo{height:120px;width:200px}
.show h3{font-size:14px;font-weight:600;margin-top:12px;white-space:nowrap}
.past-card h3{font-size:15px;font-weight:600;margin-top:12px}
.date{color:var(--red);font-size:13px;margin:4px 0}
.show p,.past-card p,.feed-item p{font-size:13px;line-height:19px;color:var(--muted)}
.past{position:absolute;top:1360px;left:0;width:1200px;height:400px;background:var(--band-dark)}
.past .section-title{margin-top:28px}
.past-card{position:absolute;top:110px;width:510px;height:270px;background:var(--card);border:1px solid #d5d5d5;padding:16px}
.past-card .photo{position:absolute;left:16px;top:16px;width:200px;height:130px}
.past-card .body{position:absolute;left:234px;top:4px;right:16px}
.links{position:absolute;left:16px;top:158px;font-size:13px;line-height:26px}
.links a{color:var(--red);text-decoration:underline;display:flex;align-items:center;gap:8px}
.links svg{flex:none}
.feeds{position:absolute;top:1760px;left:0;width:1200px;height:300px}
.feed{position:absolute;top:22px;width:500px}
.feed-head{display:flex;align-items:center;gap:12px;font-family:'Raleway',sans-serif;font-weight:300;font-size:40px;line-height:48px}
.feed-head i{width:34px;height:34px;border-radius:50%;background:var(--ink);display:block}
.feed-box{margin-top:12px;background:var(--band);padding:12px 16px;height:206px;overflow:hidden}
.feed-item{display:flex;gap:14px;margin-bottom:12px}
.feed-item .thumb{width:56px;height:64px;flex:none}
.feed-item h4{font-size:13px;font-weight:600}
.feed-item .date{font-size:12px;margin:2px 0 0}
.site-footer{position:absolute;top:2060px;left:0;width:1200px;height:180px;background:var(--footer);color:#ddd}
.foot-nav{position:absolute;left:56px;top:26px;display:flex;gap:22px;font-size:14px}
.copy{position:absolute;left:56px;top:58px;font-size:13px;color:#bbb}
.social{position:absolute;left:56px;top:100px;display:flex;gap:12px}
.social i{width:40px;height:40px;border-radius:50%;background:#888;display:block}
.partner{position:absolute;right:80px;top:58px;display:flex;align-items:center;gap:14px;font-family:'Raleway',sans-serif;font-weight:600;font-size:42px;color:#eee}
.partner i{width:22px;height:22px;background:#eee;display:block}
</style>
</head>
<body>
<header class="site-header">
  <div class="brand">Halvorsen Show</div>
  <div class="search">Search
    <svg width="14" height="14" viewBox="0 0 14 14"><circle cx="6" cy="6" r="4.5" fill="none" stroke="#999" stroke-width="1.6"/><line x1="9.5" y1="9.5" x2="13" y2="13" stroke="#999" stroke-width="1.6"/></svg>
  </div>
  <nav class="main-nav"><a class="active">Home</a><a>About Us</a><a>Upcoming Shows</a><a>Past Shows</a><a>Events</a><a>Blog</a><a>Contact</a></nav>
</header>

<section class="hero" role="img" aria-label="Photo of the host speaking with a headset microphone against a dark background">
  <div class="hero-text"><div class="lead">Helping Companies</div><div class="rest">Boost Innovation</div></div>
  <span class="btn">Read More</span>
  <span class="hero-arrow left"><svg width="36" height="56" viewBox="0 0 36 56"><polyline points="21,20 13,28 21,36" fill="none" stroke="#fff" stroke-width="2"/></svg></span>
  <span class="hero-arrow right"><svg width="36" height="56" viewBox="0 0 36 56"><polyline points="15,20 23,28 15,36" fill="none" stroke="#fff" stroke-width="2"/></svg></span>
</section>

<section class="about">
  <h2 class="section-title">About Halvorsen Show</h2>
  <p>Lorem ipsum dolor sit amet, consectetur adipisicing elit, sed do eiusmod tempor incididunt ut labore et dolore magna aliqua. Ut enim ad minim veniam, quis nostrud exercitation ullamco laboris nisi ut aliquip ex ea commodo consequat. Duis aute irure dolor in reprehenderit in voluptate velit esse cillum dolore eu fugiat nulla pariatur. Excepteur sint occaecat cupidatat non proident.</p>
</section>

<section class="upcoming">
  <h2 class="section-title">Upcoming Shows</h2>
  <div class="pager" style="top:36px"><i></i><i></i></div>
  <div class="show-row">
    <article class="show"><div class="photo" role="img" aria-label="Guest speaking on stage" style="background:linear-gradient(135deg,#6d8fb3,#2f4a6e)"></div><h3>Lorem ipsum dolor sit amet.</h3><div class="date">Feb 22, 2014</div><p>Consectetur adipisicing elit, sed do eiusmod tempor incididunt ut labore et dolore magna aliqua.</p></article>
    <article class="show"><div class="photo" role="img" aria-label="Host with headset microphone" style="background:linear-gradient(135deg,#3a2f2a,#8a6a55)"></div><h3>Lorem ipsum dolor sit amet.</h3><div class="date">Feb 22, 2014</div><p>Consectetur adipisicing elit, sed do eiusmod tempor incididunt ut labore et dolore magna aliqua.</p></article>
    <article class="show"><div class="photo" role="img" aria-label="Guest presenting to an audience" style="background:linear-gradient(135deg,#9ab3cf,#4f6c8c)"></div><h3>Lorem ipsum dolor sit amet.</h3><div class="date">Feb 22, 2014</div><p>Consectetur adipisicing elit, sed do eiusmod tempor incididunt ut labore et dolore magna aliqua.</p></article>
  </div>
</section>

<section class="past">
  <h2 class="section-title">Past Shows</h2>
  <div class="pager" style="top:40px"><i></i><i></i></div>
  <article class="past-card" style="left:80px">
    <div class="photo" role="img" aria-label="Guest speaking at an event" style="background:linear-gradient(135deg,#7fa3c8,#355478)"></div>
    <div class="links">
      <a><svg width="14" height="14"><circle cx="7" cy="4" r="3" fill="#555"/><rect x="2" y="8" width="10" height="6" rx="3" fill="#555"/></svg>Daniel Reyes</a>
      <a><svg width="14" height="14"><circle cx="7" cy="7" r="6" fill="none" stroke="#555" stroke-width="1.5"/><line x1="1" y1="7" x2="13" y2="7" stroke="#555"/></svg>www.reyesworks-example.com</a>
      <a><svg width="14" height="14"><rect x="2" y="1" width="10" height="12" fill="#555"/></svg>Book Name</a>
    </div>
    <div class="body"><h3>Lorem ipsum dolor sit amet.</h3><div class="date">Feb 22, 2014</div><p>Consectetur adipisicing elit, sed do eiusmod tempor incididunt ut labore et dolore magna aliqua. Ut enim ad minim veniam, quis nostrud exercitation ullamco laboris nisi ut aliquip ex ea commodo consequat aute irure dolor in velit esse.</p></div>
  </article>
  <article class="past-card" style="left:610px">
    <div class="photo" role="img" aria-label="Host with headset microphone" style="background:linear-gradient(135deg,#3a2f2a,#8a6a55)"></div>
    <div class="links">
      <a><svg width="14" height="14"><circle cx="7" cy="4" r="3" fill="#555"/><rect x="2" y="8" width="10" height="6" rx="3" fill="#555"/></svg>Daniel Reyes</a>
      <a><svg width="14" height="14"><circle cx="7" cy="7" r="6" fill="none" stroke="#555" stroke-width="1.5"/><line x1="1" y1="7" x2="13" y2="7" stroke="#555"/></svg>www.reyesworks-example.com</a>
      <a><svg width="14" height="14"><rect x="2" y="1" width="10" height="12" fill="#555"/></svg>Book Name</a>
    </div>
    <div class="body"><h3>Lorem ipsum dolor sit amet.</h3><div class="date">Feb 22, 2014</div><p>Consectetur adipisicing elit, sed do eiusmod tempor incididunt ut labore et dolore magna aliqua. Ut enim ad minim veniam, quis nostrud exercitation ullamco laboris nisi ut aliquip ex ea commodo consequat aute irure dolor in velit esse.</p></div>
  </article>
</section>

<section class="feeds">
  <div class="feed" style="left:80px">
    <div class="feed-head"><i></i>Chirper feed</div>
    <div class="feed-box">
      <div class="feed-item"><div class="thumb" role="img" aria-label="Profile photo" style="background:linear-gradient(135deg,#8a6a55,#3a2f2a)"></div><div><h4>Lorem ipsum dolor sit amet.</h4><p>Consectetur adipisicing elit, sed do eiusmod tempor incididunt ut labore.</p><div class="date">Feb 22, 2014</div></div></div>
      <div class="feed-item"><div class="thumb" role="img" aria-label="Profile photo" style="background:linear-gradient(135deg,#7fa3c8,#355478)"></div><div><h4>Lorem ipsum dolor sit amet.</h4><p>Consectetur adipisicing elit, sed do eiusmod tempor incididunt ut labore.</p><div class="date">Feb 22, 2014</div></div></div>
    </div>
  </div>
  <div class="feed" style="left:620px">
    <div class="feed-head"><i></i>Blog</div>
    <div class="feed-box">
      <div class="feed-item"><div class="thumb" role="img" aria-label="Book cover" style="background:linear-gradient(135deg,#c9a24a,#7a3a2a)"></div><div><h4>Lorem ipsum dolor sit amet.</h4><p>Consectetur adipisicing elit, sed do eiusmod tempor incididunt ut labore.</p><div class="date">Feb 22, 2014</div></div></div>
      <div class="feed-item"><div class="thumb" role="img" aria-label="Book cover" style="background:linear-gradient(135deg,#5a7a9a,#2a3a4a)"></div><div><h4>Lorem ipsum dolor sit amet.</h4><p>Consectetur adipisicing elit, sed do eiusmod tempor incididunt ut labore.</p><div class="date">Feb 22, 2014</div></div></div>
    </div>
  </div>
</section>

<footer class="site-footer">
  <nav class="foot-nav"><span>Home</span><span>About Us</span><span>Upcoming Shows</span><span>Past Shows</span><span>Events</span><span>Blog</span><span>Contact</span></nav>
  <div class="copy">All Rights Reserved. Copyright © 2014</div>
  <div class="social"><i></i><i></i><i></i><i></i></div>
  <div class="partner"><i></i>OrbitalWave</div>
</footer>
</body>
</html>
```